Corvane Business Cards

Front of business card will have logo, name, address, & telephone number. Back of card will have a list of services provided - Roads, Substation Pads, Temporary Pads, Site Pads, Land Leveling, Powerline Row Cleaning, Land Clearing, Gates, Fencing, Construction Entrances, Excavation, Trenching, Underground Utilities, Directional Boring, Pile Driving. We are a construction company that uses heavy equipment like bulldozers, motor graders/blades, dump trucks, backhoes, hydro axes, & skid loaders. We build roads, pads, & install electric utility lines & waterlines underground. This logo is new. The word "Construction" can be smaller as uploaded 2 example edited logos. We will be using this card design for many employees.
Target Market(s)
Industrial Electric Powerline, Wind Turbine, Solar Panel, & Water Utility companies.
Contact Information for Business Card
Name/Position - Dwayne Halster - Owner
Address: 4875 FM 309
Merkel, TX 79412
Phone number - (325) 482-5096

```html
<!DOCTYPE html>
<html lang="en">
<head>
<meta charset="utf-8">
<title>Corvane Business Cards</title>
<link href="https://fonts.googleapis.com/css2?family=Arimo:wght@400;700&display=swap" rel="stylesheet">
<style>
  :root {
    --backdrop: #d6d6d6;
    --card-white: #ffffff;
    --maroon: #3a0f18;
    --maroon-ink: #3d1119;
    --text-dark: #2b2b2b;
    --rule: #9a9a9a;
    --on-maroon: #ffffff;
  }
  * { box-sizing: border-box; margin: 0; padding: 0; }
  html, body {
    width: 1200px; height: 802px; overflow: hidden;
    background: var(--backdrop);
    font-family: "Arimo", Arial, sans-serif;
  }
  .stage { position: relative; width: 1200px; height: 802px; }
  .card {
    position: absolute; top: 274px;
    width: 443px; height: 265px;
    box-shadow: 3px 4px 8px rgba(0,0,0,0.35);
  }
  .card-front { left: 136px; background: var(--card-white); }
  .card-back  { left: 608px; background: var(--maroon); color: var(--on-maroon); }

  .brand {
    position: absolute; left: 30px; top: 104px;
    display: flex; align-items: center; gap: 10px;
    color: var(--maroon-ink); font-weight: 700;
  }
  .brand-mark { width: 14px; height: 14px; background: var(--maroon-ink); flex: none; }
  .brand-name { font-size: 34px; letter-spacing: 1px; line-height: 1; }
  .brand-sub  { font-size: 15px; letter-spacing: 1px; line-height: 1; margin-top: 8px; }

  .divider {
    position: absolute; left: 235px; top: 75px;
    width: 2px; height: 122px; background: var(--rule);
  }
  .contact { position: absolute; left: 250px; top: 76px; color: var(--text-dark); }
  .contact-name { font-size: 16px; font-weight: 700; color: var(--maroon-ink); line-height: 19px; }
  .contact-role { font-size: 12px; line-height: 15px; letter-spacing: 0.3px; }
  .contact-phone { font-size: 18px; line-height: 22px; margin-top: 15px; }
  .contact-address { font-size: 14px; line-height: 19.5px; margin-top: 10px; }

  .services {
    position: absolute; left: 36px; top: 30px; width: 380px;
    font-size: 13px; line-height: 19.5px;
  }
  .services p + p { margin-top: 14px; }
</style>
</head>
<body>
<main class="stage">
  <section class="card card-front">
    <div class="brand">
      <span class="brand-mark"></span>
      <div>
        <div class="brand-name">CORVANE</div>
        <div class="brand-sub">CONSTRUCTION</div>
      </div>
    </div>
    <div class="divider"></div>
    <div class="contact">
      <div class="contact-name">DWAYNE HALSTER</div>
      <div class="contact-role">OWNER</div>
      <div class="contact-phone">(555) 482-5096</div>
      <div class="contact-address">4875 FM 309<br>Ashcombe, NM 88412</div>
    </div>
  </section>

  <section class="card card-back">
    <div class="services">
      <p>Roads | Substation Pads | Temporary Pads | Site Pads | Land<br>Leveling, Powerline Row Cleaning | Land Clearing | Gates<br>Fencing | Construction Entrances | Excavation | Trenching<br>Underground Utilities | Directional Boring | Pile Driving.</p>
      <p>We are a construction company that uses heavy equipment like<br>bulldozers, motor graders/blades, dump trucks, backhoes,<br>hydro axes &amp; skid loaders.</p>
      <p>We build roads, pads &amp; install electric utility lines &amp; waterlines<br>underground.</p>
    </div>
  </section>
</main>
</body>
</html>
```